Falkrin homes and renovations business card design.

Would like some new card designs utilizing my new logo that look professional. I am open to different colors on the logo or utilize the same ones we have. I like the original concept but would like to see some fresh ideas and build on what we have already done.

Target Market(s)

Custom home building industry, Real estate sales, Renovation projects.

Industry/Entity Type

Home Builder

Contact Information for Business Card

Falkrin Homes and Renovations
2871 96th Avenue
Frank, Alberta
T2R3W8
Home : 403- 718-4063 Cell: 403- 294-5170

My info is : Dax Falkrin, President and CEO
email: falkrinhomes@maildrop-example.net
Website: falkrinhomes-example.com
websit

Requirements
Must have
• Must Use my new logo design. I am open to different colors on the logo or utilize the same ones in the existing design. I can upload the original logo design if needed.

```html
<!DOCTYPE html>
<html lang="en">
<head>
<meta charset="utf-8">
<title>Falkrin Homes and Renovations – Business Card</title>
<link rel="stylesheet" href="https://fonts.googleapis.com/css2?family=Oswald:wght@500&family=Open+Sans:wght@400;600&display=swap">
<style>
  :root {
    --backdrop: #2b2b2d;
    --card-dark: #1f1f20;
    --card-light: #ffffff;
    --gold: #b8892f;
    --ink: #555555;
    --ink-soft: #6a6a6a;
    --rule: #9a9a9a;
  }
  * { box-sizing: border-box; margin: 0; padding: 0; }
  html, body {
    width: 1200px;
    height: 1000px;
    overflow: hidden;
    background: var(--backdrop);
  }
  .stage {
    position: relative;
    width: 1200px;
    height: 1000px;
  }
  .card {
    position: absolute;
    left: 250px;
    width: 700px;
    height: 400px;
    box-shadow: 0 10px 30px rgba(0, 0, 0, 0.45);
  }
  .card-front {
    top: 60px;
    background: var(--card-dark);
    display: flex;
    align-items: center;
    justify-content: center;
  }
  .brand {
    display: flex;
    align-items: center;
    gap: 12px;
    font-family: "Open Sans", sans-serif;
    font-weight: 600;
    font-size: 26px;
    letter-spacing: 1px;
    color: var(--gold);
  }
  .brand-mark {
    width: 14px;
    height: 14px;
    background: var(--gold);
  }
  .card-back {
    top: 540px;
    background: var(--card-light);
  }
  .identity {
    position: absolute;
    right: 385px;
    top: 130px;
    text-align: right;
  }
  .person-name {
    font-family: "Oswald", sans-serif;
    font-weight: 500;
    font-size: 38px;
    line-height: 1.1;
    letter-spacing: 1px;
    color: var(--ink);
  }
  .person-role {
    font-family: "Open Sans", sans-serif;
    font-weight: 600;
    font-size: 17px;
    color: var(--gold);
  }
  .divider {
    position: absolute;
    left: 342px;
    top: 120px;
    width: 2px;
    height: 110px;
    background: var(--rule);
  }
  .contacts {
    position: absolute;
    left: 362px;
    top: 122px;
    list-style: none;
    font-family: "Open Sans", sans-serif;
    font-size: 17px;
    color: var(--ink-soft);
  }
  .contacts li {
    display: flex;
    align-items: center;
    gap: 12px;
    height: 26px;
  }
  .contacts svg {
    width: 14px;
    height: 14px;
    flex: none;
  }
  .web-name { color: var(--gold); }
  .address {
    position: absolute;
    left: 200px;
    top: 318px;
    display: flex;
    align-items: center;
    gap: 10px;
    font-family: "Open Sans", sans-serif;
    font-size: 19px;
    color: var(--ink-soft);
  }
  .address svg { width: 18px; height: 18px; }
</style>
</head>
<body>
<main class="stage">
  <section class="card card-front">
    <div class="brand">
      <span class="brand-mark"></span>
      <span class="brand-name">Falkrin Homes and Renovations</span>
    </div>
  </section>

  <section class="card card-back">
    <div class="identity">
      <h1 class="person-name">DAX FALKRIN</h1>
      <p class="person-role">President and CEO</p>
    </div>
    <div class="divider"></div>
    <ul class="contacts">
      <li>
        <svg viewBox="0 0 16 16" aria-hidden="true"><path fill="#b8892f" d="M3.5 1l2.5 3-1.5 1.5c.8 2 2.5 3.7 4.5 4.5L10.5 8.5l3 2.5-1.5 3C6 14 2 10 2 2.5z"/></svg>
        <span>403 718 4063</span>
      </li>
      <li>
        <svg viewBox="0 0 16 16" aria-hidden="true"><rect x="4" y="1" width="8" height="14" rx="1.5" fill="none" stroke="#b8892f" stroke-width="1.5"/><circle cx="8" cy="12.5" r="0.9" fill="#b8892f"/></svg>
        <span>403 294 5170</span>
      </li>
      <li>
        <svg viewBox="0 0 16 16" aria-hidden="true"><rect x="1" y="3" width="14" height="10" fill="#b8892f"/><path d="M1 3l7 6 7-6" fill="none" stroke="#fff" stroke-width="1.2"/></svg>
        <span>falkrinhomes@maildrop-example.net</span>
      </li>
      <li>
        <svg viewBox="0 0 16 16" aria-hidden="true"><circle cx="9.5" cy="6.5" r="4.5" fill="none" stroke="#b8892f" stroke-width="1.6"/><path d="M6.3 9.7L1.5 14.5" stroke="#b8892f" stroke-width="2"/></svg>
        <span>www.<span class="web-name">falkrinhomes-example</span>.com</span>
      </li>
    </ul>
    <p class="address">
      <svg viewBox="0 0 18 18" aria-hidden="true"><path d="M16 2L2 8l6 2 2 6z" fill="none" stroke="#b8892f" stroke-width="1.4" stroke-linejoin="round"/></svg>
      <span>2871 96th Avenue Frank, Alberta</span>
    </p>
  </section>
</main>
</body>
</html>
```